Corvexa Background Design

Need to develop a Corvexa Background picture for my profile. The components I want in there are:
1) Name: Abhrajit Dutta
2) Key Skills: Strategy, Innovation, Execution, Growth and Leadership
3) A photograph (an action photograph) The attached photograph is an example.
A black background would be ideal.

The design should meet the Corvexa background size requirements.

The background should reinforce an image of a thinking person but equally capable of implementing.

Leadership

```html
<!DOCTYPE html>
<html lang="en">
<head>
<meta charset="utf-8">
<title>Abhrajit Dutta – Corvexa Background</title>
<link rel="stylesheet" href="https://fonts.googleapis.com/css2?family=Arimo:wght@400;700&family=Crimson+Text:wght@400&family=Great+Vibes&display=swap">
<style>
:root{
  --stage:#d8d8d8;
  --ink:#000;
  --name-orange:#f28a1e;
  --white:#fff;
  --bar-top:#474747;
  --bar-top-dark:#333;
  --bar-nav:#1f1f1f;
  --link:#2a7ab8;
  --nav-link:#5fb0e8;
  --green:#a6d23c;
  --page:#e6e6e6;
  --panel:#fff;
  --soft-panel:#f4f4f4;
  --rule:#d0d0d0;
  --text:#222;
}
*{box-sizing:border-box;margin:0;padding:0}
html,body{width:1200px;height:964px;overflow:hidden}
body{position:relative;background:var(--stage);font-family:"Arimo",Arial,sans-serif;color:var(--text)}
.abs{position:absolute}

/* Banner component */
.banner{position:absolute;overflow:hidden;background:
  radial-gradient(ellipse 45% 40% at 42% 92%,rgba(150,150,150,.75),rgba(60,60,60,.35) 55%,rgba(0,0,0,0) 100%),var(--ink)}
.banner--hero{left:142px;top:74px;width:943px;height:286px;font-size:20px}
.banner--page{left:14px;top:541px;width:779px;height:266px;font-size:17px}
.banner__name{position:absolute;left:43%;top:14%;transform:translateX(-50%);font-family:"Great Vibes",cursive;color:var(--name-orange);font-size:2.6em;white-space:nowrap;line-height:1.2}
.banner__skills{position:absolute;left:15%;top:41%;font-family:"Crimson Text",Georgia,serif;color:var(--white);font-size:1.05em;white-space:nowrap}
.banner__photo{position:absolute;left:71%;top:16%;width:24%;height:84%;
  background:linear-gradient(180deg,#2b2b2b 0%,#4a4a4e 45%,#6b5637 75%,#8a6a3c 100%)}

/* Header bars */
.topbar{left:0;top:388px;width:1200px;height:41px;background:linear-gradient(#555,var(--bar-top-dark));color:var(--white);font-size:14px}
.brand{position:absolute;left:17px;top:8px;display:flex;align-items:center;gap:6px;font-size:22px;font-weight:700;color:var(--white)}
.brand__mark{width:14px;height:14px;background:var(--nav-link)}
.account{position:absolute;left:141px;top:13px;font-weight:700;font-size:14px}
.account a{color:var(--nav-link);font-weight:400}
.icon-mail{position:absolute;left:371px;top:13px}
.icon-flag{position:absolute;left:416px;top:11px}
.user{position:absolute;left:905px;top:12px;font-weight:700;font-size:16px}
.add-conn{position:absolute;left:1059px;top:11px;font-weight:700;font-size:16px;color:var(--green)}

.navbar{left:0;top:429px;width:1200px;height:47px;background:var(--bar-nav)}
.nav{position:absolute;left:15px;top:15px;display:flex;gap:0;font-size:16px}
.nav span{color:var(--nav-link);margin-right:19px}
.nav .is-current{color:var(--white)}
.search-scope{position:absolute;left:704px;top:7px;width:120px;height:31px;background:#444;border-radius:3px 0 0 3px;color:var(--white);font-size:15px;font-weight:700;padding:7px 0 0 12px}
.search{position:absolute;left:824px;top:7px;width:363px;height:31px;background:var(--white);color:#999;font-size:15px;padding:7px 0 0 6px}
.search svg{position:absolute;right:10px;top:7px}

/* Page */
.page{left:0;top:476px;width:1200px;height:488px;background:var(--page)}
.info-strip{left:14px;top:476px;width:779px;height:52px;background:var(--soft-panel);border-bottom:2px solid var(--rule)}
.info-strip a{position:absolute;left:73px;top:12px;color:var(--link);font-size:15px;text-decoration:none}

.updates{left:14px;top:819px;width:779px;height:145px;background:var(--panel)}
.updates__tab{position:absolute;left:0;top:0;width:192px;height:42px;background:#2a2a2a;color:var(--white);font-weight:700;font-size:17px;padding:11px 0 0 25px}
.updates__lead{position:absolute;left:25px;top:61px;width:720px;font-size:16px;line-height:21px}
.updates__lead b{color:var(--link)}
.updates__thumb{position:absolute;left:25px;top:112px;width:217px;height:40px;background:linear-gradient(#6f8ea8,#4b6c88)}
.updates__title{position:absolute;left:260px;top:113px;width:460px;font-weight:700;font-size:17px;line-height:21px;color:#111}

.sidebar{left:805px;top:476px;width:395px;height:488px;background:var(--panel)}
.products__head{position:absolute;left:24px;top:29px;font-size:18px;color:#111}
.products__desc{position:absolute;left:24px;top:70px;width:320px;font-size:14px;line-height:17px}
.products__add{position:absolute;right:38px;top:128px;color:var(--link);font-size:15px}
.products__rule{position:absolute;left:24px;top:170px;width:340px;height:1px;background:var(--rule)}

.ads{position:absolute;left:14px;top:195px;width:357px;height:300px;background:#f5f5f5;border:1px solid #e2e2e2;border-radius:6px}
.ads__badge{position:absolute;left:-4px;top:7px;width:38px;height:24px;background:#5b9fd1}
.ads__label{position:absolute;left:46px;top:12px;font-size:13px;color:#444}
.ad{position:absolute;left:12px;width:330px;height:65px}
.ad__thumb{position:absolute;left:0;top:0;width:65px;height:65px;border:1px solid #ccc;background:var(--white)}
.ad__title{position:absolute;left:72px;top:0;font-weight:700;font-size:15px;color:var(--link)}
.ad__text{position:absolute;left:72px;top:19px;width:260px;font-size:13px;line-height:17px;color:#111}
</style>
</head>
<body>

<section class="banner banner--hero">
  <div class="banner__name">Abhrajit Dutta</div>
  <div class="banner__skills">Strategy, Innovation, Execution, Growth and Leadership</div>
  <div class="banner__photo" role="img" aria-label="Action photograph of the speaker at a wooden podium, arm raised and pointing upward"></div>
</section>

<header class="abs topbar">
  <div class="brand"><span>Corvexa</span><span class="brand__mark"></span></div>
  <div class="account">Account Type: Basic | <a>Upgrade</a></div>
  <svg class="icon-mail" width="20" height="14" viewBox="0 0 20 14"><rect x="1" y="1" width="18" height="12" fill="none" stroke="#fff" stroke-width="2"/><path d="M1 1l9 7 9-7" fill="none" stroke="#fff" stroke-width="2"/></svg>
  <svg class="icon-flag" width="16" height="18" viewBox="0 0 16 18"><path d="M2 1v17" stroke="#fff" stroke-width="2"/><path d="M3 2h12l-3 4 3 4H3z" fill="#fff"/></svg>
  <div class="user">Riya Menon ▾</div>
  <div class="add-conn">Add Connections</div>
</header>

<nav class="abs navbar">
  <div class="nav"><span>Home</span><span>Profile</span><span>Contacts</span><span>Groups</span><span>Jobs</span><span>Inbox</span><span class="is-current">Companies</span><span>News</span><span>More</span></div>
  <div class="search-scope">Companies ▾</div>
  <div class="search">Search...
    <svg width="18" height="18" viewBox="0 0 18 18"><circle cx="7" cy="7" r="5.5" fill="none" stroke="#2a7ab8" stroke-width="2.5"/><path d="M11 11l6 6" stroke="#2a7ab8" stroke-width="3"/></svg>
  </div>
</nav>

<div class="abs page"></div>
<div class="abs info-strip"><a>See more helpful information on Company Pages ▸</a></div>

<section class="banner banner--page">
  <div class="banner__name">Abhrajit Dutta</div>
  <div class="banner__skills">Strategy, Innovation, Execution, Growth and Leadership</div>
  <div class="banner__photo" role="img" aria-label="Action photograph of the speaker at a wooden podium, arm raised and pointing upward"></div>
</section>

<section class="abs updates">
  <div class="updates__tab">RECENT UPDATES</div>
  <p class="updates__lead"><b>Harbor Reach</b> How to use Chirpline chats to capitalize on an engaged community to further grow your audience and brand.</p>
  <div class="updates__thumb" role="img" aria-label="Article thumbnail graphic"></div>
  <p class="updates__title">How To Participate In Chirpline Chats &amp; Stop Being Socially Awkward</p>
</section>

<aside class="abs sidebar">
  <h2 class="products__head">PRODUCTS</h2>
  <p class="products__desc">Drive new leads and sales by showcasing what your business has to offer.</p>
  <div class="products__add">Add a product or service ▸</div>
  <div class="products__rule"></div>

  <div class="ads">
    <div class="ads__badge"></div>
    <div class="ads__label">Ads by Corvexa Members</div>

    <div class="ad" style="top:48px">
      <div class="ad__thumb" role="img" aria-label="Photograph of a wedding couple" style="background:linear-gradient(#f2f2f2,#cfc8c4)"></div>
      <div class="ad__title">Photography Jobs &amp; Leads</div>
      <p class="ad__text">Receive Quality Jobs For Photographers. Get Phone &amp; Email Alerts Daily!</p>
    </div>

    <div class="ad" style="top:135px">
      <div class="ad__thumb">
        <svg width="63" height="63" viewBox="0 0 63 63"><circle cx="30" cy="34" r="22" fill="#a9d0ef"/><path d="M30 34V12a22 22 0 0 1 22 22z" fill="#fff"/><rect x="40" y="8" width="4" height="12" fill="#c8dff0"/><rect x="46" y="4" width="4" height="16" fill="#c8dff0"/><rect x="52" y="10" width="4" height="10" fill="#c8dff0"/></svg>
      </div>
      <div class="ad__title">CMO's Marketing Dashboard</div>
      <p class="ad__text">Evaluate Online &amp; Offline Marketing Effectiveness In One Simple Dashboard!</p>
    </div>

    <div class="ad" style="top:222px">
      <div class="ad__thumb" role="img" aria-label="Photograph of a student at a laptop" style="background:linear-gradient(#3b4f6a,#1f2a3a)"></div>
      <div class="ad__title">MS in Internet Marketing</div>
      <p class="ad__text">Get a Master's in Internet Marketing, w/ classes in SEO. Learn more now!</p>
    </div>
  </div>
</aside>

</body>
</html>
```